Corvel Capital LLC

Need Professional Business cards for New Investment Fund

Target Market(s)

High Quality investors

Industry/Entity Type

Financial

Contact Information for Business Card

Phone Number +1 555 284 6190
Name Lukas Varenko
Title Fund Manager
email lv@FundCorvel.com
Website www.FundCorvel.com

Colors

Designer to choose colors to be used in the design.

Requirements
Must have
• Must have our Logo and all of the above. Must be made so lettering and loge can be raised

```html
<!DOCTYPE html>
<html lang="en">
<head>
<meta charset="utf-8">
<title>Quillmont – Business Card</title>
<link href="https://fonts.googleapis.com/css2?family=Roboto:wght@400;500;700&display=swap" rel="stylesheet">
<style>
  :root {
    --page-bg: #d9d6cf;
    --card-light: #ecebe6;
    --card-dark: #414a3b;
    --accent-green: #4fa23a;
    --line-light: #d9d4c8;
    --text-light: #d6d8cf;
    --text-muted: #bfc2b6;
  }
  html, body {
    margin: 0;
    padding: 0;
    width: 1200px;
    height: 1047px;
    overflow: hidden;
    background: var(--page-bg);
    font-family: "Roboto", Arial, sans-serif;
  }
  .business-card {
    position: absolute;
    left: 150px;
    top: 290px;
    width: 945px;
    height: 513px;
    border-radius: 24px;
    overflow: hidden;
    background: var(--card-light);
    box-shadow: 0 10px 30px rgba(0,0,0,0.18);
  }
  .card-shapes {
    position: absolute;
    inset: 0;
  }
  .brand-name {
    position: absolute;
    left: 96px;
    top: 232px;
    margin: 0;
    font-size: 40px;
    line-height: 48px;
    font-weight: 500;
    color: var(--accent-green);
  }
  .contact-block {
    position: absolute;
    left: 587px;
    top: 0;
    width: 340px;
    height: 100%;
    color: var(--text-light);
  }
  .person-name {
    position: absolute;
    top: 120px;
    left: 0;
    margin: 0;
    font-size: 26px;
    line-height: 32px;
    font-weight: 700;
    color: var(--accent-green);
  }
  .person-title {
    position: absolute;
    top: 156px;
    left: 0;
    margin: 0;
    font-size: 20px;
    line-height: 26px;
    font-weight: 400;
    color: var(--text-muted);
  }
  .divider {
    position: absolute;
    top: 238px;
    left: 0;
    width: 26px;
    height: 3px;
    background: var(--text-muted);
  }
  .contact-list {
    position: absolute;
    top: 277px;
    left: 0;
    list-style: none;
    margin: 0;
    padding: 0;
  }
  .contact-item {
    display: flex;
    align-items: center;
    gap: 12px;
    font-size: 19.5px;
    line-height: 36px;
    white-space: nowrap;
    color: var(--text-light);
  }
  .contact-icon {
    width: 15px;
    height: 15px;
    flex: none;
  }
</style>
</head>
<body>
  <div class="business-card">
    <svg class="card-shapes" width="945" height="513" viewBox="0 0 945 513">
      <rect x="422" y="0" width="523" height="513" fill="var(--card-dark)"/>
      <polyline points="492,0 492,357 540,357 427,513" fill="none" stroke="var(--line-light)" stroke-width="4"/>
    </svg>

    <p class="brand-name">Quillmont</p>

    <div class="contact-block">
      <h1 class="person-name">Lukas Varenko</h1>
      <p class="person-title">Fund Manager</p>
      <div class="divider"></div>
      <ul class="contact-list">
        <li class="contact-item">
          <svg class="contact-icon" viewBox="0 0 16 16"><rect x="4" y="1" width="8" height="14" rx="1.5" fill="none" stroke="var(--accent-green)" stroke-width="1.8"/><circle cx="8" cy="12.3" r="0.9" fill="var(--accent-green)"/></svg>
          <span>+1 555 284 6190</span>
        </li>
        <li class="contact-item">
          <svg class="contact-icon" viewBox="0 0 16 16"><rect x="1" y="3" width="14" height="10" rx="1" fill="var(--accent-green)"/><polyline points="1.5,4 8,9 14.5,4" fill="none" stroke="var(--card-dark)" stroke-width="1.4"/></svg>
          <span>lv@FundCorvel.com</span>
        </li>
        <li class="contact-item">
          <svg class="contact-icon" viewBox="0 0 16 16"><circle cx="8" cy="8" r="7" fill="var(--accent-green)"/><path d="M1 8h14M8 1c-3 3-3 11 0 14M8 1c3 3 3 11 0 14" fill="none" stroke="var(--card-dark)" stroke-width="1"/></svg>
          <span>www.FundCorvel.com</span>
        </li>
      </ul>
    </div>
  </div>
</body>
</html>
```